Stationery Design Project

We need a stationery design for our Norwegian trucking company. We have existed for about 15 years and our 12 drivers uses relatively new vehicles to transport goods around in northern Norway. Long distance routes with fresh fish og food transport is our main operations.

We have already made alogo that's printed on our trucks. The logo and a picture of our trucks is attached. I think the logo i crappy, but since its already in use, changing it is not an option in this round. Still using a better colour scheme in the overall stationery and more interesting fonts is possible (altso in the logo).

Company details:
Name: Kjelvraket AS
Organisation nr 873 615 309
Post adress: 8642 Raudvik

I like minimalism and simplicity. I am avalibly for questions in normal GMT working hours either here or on mail: ivar@fjordlast.no

Reason: Hi. Im extending the deadline because I needed some time to find a vector file of our logo. Sorry for the inconvenience

Hi, and thanks for all your interest in the project. Some updates:

-          I have decided to commit to using one of the designs. Some designer will get the payment.

-          I have extended the deadline with 24 hours since I needed some time to find our firms vector logo (a slow Swedish man was holding me up)

-          We will not choose a design before the deadline. No need to rush.

-          We have received a lot of great design and think there is a need to specified the product we want to make:

o   Business Card for all our employers. I just need the design and will duplicate with the correct numbers and name myself. The information on should be: Logo, employer’s name, Phone number, email, website, Postal number and address. Use this as a template: logo, Leif Brattvoll, 47382066, Leif@fjordlast.no,, fjordlast.no, 8642 Raudvik. The order and placement of the information is your creative decision.

o   Stickers to put on the goods we travel. On the sticker the should be the following information: Logo, phone number, Tekst and link: Fraktæ av Kjelvraket. Ke du syns? Fjordlast.no/tilbakemelding (this means: Handled by Kjelvraket. What do you think Fjordlast.no/feedback -à the link will be a feedback form). The placement the information and size is your creative decision with some stings: we have been thinking of using Drukko for printing and see that a size about 6x6 cm, 8x5 or something like that. (with 3000 copies our budget is 200 punds). Any suggestions of other suppliers are welcome. Drukko price calculator http://www.drukkolabelhouse.co.uk/digital-litho-printing/printing-labels-tags/stickers/

o   Letterhead with logo, address, phone number and organizational number.

o   Envelopes with logo,address, phone number and organizational number.

Have a nice day.

 

 

• Using the blue colour in the logo and using a similar graphic approch.

```html
<!DOCTYPE html>
<html lang="no">
<head>
<meta charset="utf-8">
<title>Kjelvraket AS – Stationery</title>
<link href="https://fonts.googleapis.com/css2?family=Open+Sans:wght@300;400;600;700&display=swap" rel="stylesheet">
<style>
  :root {
    --backdrop: #a6a6a6;
    --paper: #ffffff;
    --brand-deep: #223f98;
    --brand-mid: #1f6aa8;
    --brand-light: #1f86b4;
    --brand-text: #1e4fa0;
    --ink-soft: #6d6d6d;
    --grey-light: #d6d6d6;
    --grey-dark: #7a7a7a;
  }
  * { margin: 0; padding: 0; box-sizing: border-box; }
  html, body { width: 1200px; height: 900px; overflow: hidden; background: var(--backdrop); }
  body { font-family: "Open Sans", Arial, sans-serif; }
  .stage { position: relative; width: 1200px; height: 900px; }

  .wordmark { display: flex; align-items: center; gap: 6px; font-weight: 700; color: var(--brand-text); white-space: nowrap; }
  .wordmark .dot { border-radius: 50%; background: currentColor; flex: none; }

  /* footer band: straight grey rule + blue gradient strip */
  .footer-band { position: absolute; left: 0; right: 0; bottom: 0; }
  .footer-band .rule { height: 4px; background: linear-gradient(90deg, var(--grey-light), var(--grey-dark) 50%, var(--grey-light)); }
  .footer-band .gap { height: 2px; background: var(--paper); }
  .footer-band .strip { background: linear-gradient(90deg, var(--brand-deep) 0%, var(--brand-light) 55%, var(--brand-deep) 100%); }

  /* business card – front */
  .card-front {
    position: absolute; left: 60px; top: 46px; width: 252px; height: 144px; border-radius: 9px;
    background: radial-gradient(ellipse at 45% 80%, var(--brand-light) 0%, var(--brand-mid) 40%, var(--brand-deep) 100%);
    display: flex; align-items: center; justify-content: center;
  }
  .card-front .wordmark { color: var(--paper); font-size: 20px; }
  .card-front .wordmark .dot { width: 10px; height: 10px; }

  /* business card – back */
  .card-back { position: absolute; left: 238px; top: 214px; width: 252px; height: 144px; border-radius: 9px; background: var(--paper); overflow: hidden; }
  .card-back .wordmark { position: absolute; left: 14px; top: 42px; font-size: 15px; }
  .card-back .wordmark .dot { width: 8px; height: 8px; }
  .card-back .holder { position: absolute; left: 160px; top: 31px; }
  .holder-name { font-size: 8.5px; font-weight: 600; color: var(--brand-text); }
  .holder-role { font-size: 5.5px; color: var(--ink-soft); margin-top: -1px; }
  .card-back .contact { position: absolute; left: 160px; top: 68px; font-size: 5.5px; line-height: 9px; color: var(--ink-soft); }
  .card-back .footer-band .strip { height: 24px; }

  .contact-line { display: flex; align-items: center; gap: 4px; font-weight: 300; }
  .contact-line svg { flex: none; fill: var(--brand-text); }

  /* letterhead */
  .letterhead { position: absolute; left: 547px; top: 58px; width: 613px; height: 791px; background: var(--paper); overflow: hidden; }
  .letterhead .wordmark { position: absolute; left: 29px; top: 46px; font-size: 29px; }
  .letterhead .wordmark .dot { width: 14px; height: 14px; }
  .letterhead .contact { position: absolute; left: 493px; top: 54px; font-size: 9px; line-height: 12px; color: var(--ink-soft); }
  .letterhead .footer-band .strip { height: 48px; }
  .org-number { position: absolute; color: var(--paper); font-weight: 300; font-size: 9px; }
  .letterhead .org-number { right: 30px; bottom: 12px; }

  /* envelope */
  .envelope-flap { position: absolute; left: 95px; top: 382px; width: 685px; height: 96px; }
  .flap-mark { position: absolute; left: 390px; top: 411px; transform: rotate(180deg); }
  .flap-mark .wordmark { color: var(--paper); font-size: 15px; }
  .flap-mark .wordmark .dot { width: 8px; height: 8px; }
  .envelope { position: absolute; left: 95px; top: 477px; width: 685px; height: 297px; background: var(--paper); overflow: hidden; }
  .envelope .wordmark { position: absolute; left: 18px; top: 25px; font-size: 26px; }
  .envelope .wordmark .dot { width: 13px; height: 13px; }
  .envelope .contact { position: absolute; left: 22px; top: 68px; font-size: 9px; line-height: 12px; color: var(--ink-soft); }
  .envelope .footer-band .strip { height: 42px; }
  .envelope .org-number { right: 20px; bottom: 15px; }
</style>
</head>
<body>
<div class="stage">

  <svg width="0" height="0" style="position:absolute">
    <defs>
      <linearGradient id="flap-blue" x1="0" y1="0" x2="1" y2="0">
        <stop offset="0" stop-color="#2450a0"/>
        <stop offset="0.6" stop-color="#1f80b2"/>
        <stop offset="1" stop-color="#2356a3"/>
      </linearGradient>
      <symbol id="icon-house" viewBox="0 0 10 10"><path d="M5 1 L9.5 5 H8 V9 H6 V6.5 H4 V9 H2 V5 H0.5 Z"/></symbol>
      <symbol id="icon-phone" viewBox="0 0 10 10"><path d="M1 4 C1 2 9 2 9 4 L8 5.5 L6.5 4.5 V3.8 C5.5 3.4 4.5 3.4 3.5 3.8 V4.5 L2 5.5 Z M3 6 H7 L8 8.5 H2 Z"/></symbol>
      <symbol id="icon-mail" viewBox="0 0 10 10"><path d="M1 2.5 H9 V7.5 H1 Z M1.8 3.2 L5 5.6 L8.2 3.2" fill="none" stroke="currentColor" stroke-width="1"/></symbol>
      <symbol id="icon-web" viewBox="0 0 10 10"><circle cx="5" cy="5" r="4"/><path d="M1 5 H9 M5 1 V9" stroke="#fff" stroke-width="0.8"/></symbol>
    </defs>
  </svg>

  <!-- business card front -->
  <div class="card-front">
    <div class="wordmark"><span class="dot"></span>Kjelvraket</div>
  </div>

  <!-- business card back -->
  <div class="card-back">
    <div class="wordmark"><span class="dot"></span>Kjelvraket</div>
    <div class="holder">
      <div class="holder-name">Leif Brattvoll</div>
      <div class="holder-role">Marketing Manager</div>
    </div>
    <div class="contact">
      <div class="contact-line"><svg width="6" height="6"><use href="#icon-phone"/></svg>47382066</div>
      <div class="contact-line"><svg width="6" height="6" style="color:#1e4fa0"><use href="#icon-mail"/></svg>Leif@fjordlast.no</div>
      <div class="contact-line"><svg width="6" height="6"><use href="#icon-web"/></svg>www.fjordlast.no</div>
      <div class="contact-line"><svg width="6" height="6"><use href="#icon-house"/></svg>8642 Raudvik</div>
    </div>
    <div class="footer-band"><div class="rule"></div><div class="gap"></div><div class="strip"></div></div>
  </div>

  <!-- letterhead -->
  <div class="letterhead">
    <div class="wordmark"><span class="dot"></span>Kjelvraket</div>
    <div class="contact">
      <div class="contact-line"><svg width="7" height="7"><use href="#icon-house"/></svg>8642 Raudvik</div>
      <div class="contact-line"><svg width="7" height="7"><use href="#icon-phone"/></svg>47382066</div>
    </div>
    <div class="footer-band"><div class="rule"></div><div class="gap"></div><div class="strip"></div></div>
    <div class="org-number">Organisation Number 873 615 309</div>
  </div>

  <!-- envelope -->
  <svg class="envelope-flap" viewBox="0 0 685 96" preserveAspectRatio="none">
    <path d="M0 96 L24 36 Q30 26 42 25 L342 0 L635 24 Q650 26 656 36 L685 96 Z" fill="url(#flap-blue)"/>
  </svg>
  <div class="flap-mark">
    <div class="wordmark"><span class="dot"></span>Kjelvraket</div>
  </div>
  <div class="envelope">
    <div class="wordmark"><span class="dot"></span>Kjelvraket</div>
    <div class="contact">
      <div class="contact-line"><svg width="7" height="7"><use href="#icon-house"/></svg>8642 Raudvik</div>
      <div class="contact-line"><svg width="7" height="7"><use href="#icon-phone"/></svg>47382066</div>
    </div>
    <div class="footer-band"><div class="rule"></div><div class="gap"></div><div class="strip"></div></div>
    <div class="org-number">Organisation Number 873 615 309</div>
  </div>

</div>
</body>
</html>
```